UL Aesthetic improvement on full website

brightneighbourhq.com
We need someone to improve the current website brightneighbourhq.com
Some designed to fail to follow isntruction and deliver. please find attached summary latest design requirement, please follow and read each of the requirements carefully and submit max two versions only. The winner would have to deliver within 5 days

Sample reference : velmorq.com/html/brightneighbour/#
(previous winner cant deliver)
*All of our wording and graphic content are updated, designer wouldn't involve in recreating any content.
Designer may use template or own material. delivery in html and implement on our WordPress server

please submit about us the project submission.
upon the winning, you have to maintain sub content / pages and submit the full site with your improved version of full websites including inner pages

Low design quality

Target Market(s)

general audience

Industry/Entity Type

social service

Number of Pages Required

5+ page

Requirements
Must have
• feeling and look similar to pobrix dot com
Nice to have
• extend the same style to other pages

```html
<!DOCTYPE html>
<html lang="en">
<head>
<meta charset="utf-8">
<title>About Us – Bright Neighbour</title>
<link rel="stylesheet" href="https://fonts.googleapis.com/css2?family=Poppins:wght@300;400;500;600;700&display=swap">
<style>
:root{
  --coral:#f2626b;
  --coral-soft:#f7a0a6;
  --pink-wash:#fde3e5;
  --pink-mid:#fbc8cc;
  --peach:#fdd6bf;
  --butter:#fde7a8;
  --ink:#1c1c1c;
  --grey:#6b6b6b;
  --line:#e4e4e4;
  --white:#ffffff;
}
*{box-sizing:border-box;margin:0;padding:0}
html,body{width:1200px;height:4596px;overflow:hidden}
body{position:relative;background:var(--white);font-family:'Poppins',sans-serif;color:var(--ink)}
.backdrop{position:absolute;inset:0;width:1200px;height:4596px;z-index:0}
.abs{position:absolute;z-index:1}

/* header */
.brand{left:32px;top:18px;width:64px;height:64px;border-radius:50%;background:var(--coral);color:var(--white);font-size:10px;font-weight:600;display:flex;align-items:center;justify-content:center;text-align:center;line-height:1.2}
.nav{left:470px;top:34px;display:flex;gap:30px;font-size:16px;font-weight:500}
.nav a{color:var(--ink);text-decoration:none}
.nav a.active{color:var(--coral);border-bottom:2px solid var(--coral);padding-bottom:4px}
.btn-dark{background:var(--ink);color:var(--white);border-radius:30px;font-weight:600;font-size:14px;display:flex;align-items:center;justify-content:center}
.join{left:960px;top:26px;width:132px;height:46px}

/* eyebrow & headings */
.eyebrow{font-size:13px;font-weight:600;letter-spacing:1.5px;color:var(--coral);text-transform:uppercase}
.h-xl{font-size:52px;font-weight:600;line-height:1.1}
.h-lg{font-size:40px;font-weight:600;line-height:1.15}
.lead{font-size:24px;font-weight:400;line-height:1.35;color:#333}
.body-text{font-size:15px;line-height:1.7;color:var(--grey)}

/* hero */
.hero-text{left:100px;top:270px;width:420px}
.hero-text .h-xl{margin:12px 0 10px}
.hero-photo{left:552px;top:208px;width:548px;height:400px;border-radius:24px;background:linear-gradient(135deg,#c9a68a,#f3e2d3 55%,#8e7664);box-shadow:0 16px 40px rgba(0,0,0,.15)}
.badge{left:946px;top:622px;width:90px;height:44px;border-radius:22px;background:#eef0f2;border:1px solid var(--line)}

/* value cards */
.card{top:728px;width:300px;height:272px;background:var(--white);border-radius:14px;box-shadow:0 10px 30px rgba(0,0,0,.08);padding:36px 30px}
.card h3{font-size:24px;font-weight:600;margin-bottom:14px}
.card p{font-size:14px;line-height:1.65;color:var(--grey)}

/* involvement rows */
.disc{border-radius:50%}
.phone{width:170px;height:350px;border-radius:28px;background:linear-gradient(180deg,#fff 0%,#fde7e8 60%,#f7b7ba 100%);border:8px solid #2a2a2a;box-shadow:0 14px 30px rgba(0,0,0,.2)}
.involve{width:460px}
.involve .h-lg{margin:10px 0 22px;font-size:38px}
.involve p{margin-bottom:18px}

/* faq */
.faq-head{left:100px;top:2980px;width:520px}
.faq-head .h-lg{font-size:38px;margin:10px 0 8px}
.faq-list{left:100px;top:3136px;width:494px;display:flex;flex-direction:column;gap:17px}
.faq-item{height:42px;border:1px solid var(--line);border-radius:21px;padding:0 20px;display:flex;align-items:center;font-size:12px;color:#444;background:var(--white);white-space:nowrap;overflow:hidden}
.faq-photo{left:652px;top:3112px;width:448px;height:440px;border-radius:22px;background:linear-gradient(160deg,#dceaf3,#9fc3dc 60%,#5d7f98)}

/* newsletter */
.sub-title{left:100px;top:3812px;font-size:40px;font-weight:600;line-height:1.15;color:var(--coral)}
.sub-title span{color:var(--ink)}
.sub-blurb{left:100px;top:3932px;width:300px;font-size:13px;line-height:1.6;color:#555}
.field{top:3830px;height:58px;border-radius:10px;background:var(--white);font-size:15px;color:#555;padding:0 22px;display:flex;align-items:center}
.consent{left:500px;top:3928px;display:flex;align-items:center;gap:16px;font-size:15px;color:#333}
.consent i{width:24px;height:24px;border-radius:50%;background:var(--coral);display:block}
.subscribe{left:500px;top:3996px;width:172px;height:56px;font-size:15px}

/* footer */
.foot-brand{left:100px;top:4240px;width:80px;height:80px;border-radius:50%;background:var(--coral);color:var(--white);font-size:12px;font-weight:600;display:flex;align-items:center;justify-content:center;text-align:center;line-height:1.2}
.foot-follow{left:240px;top:4236px;width:400px}
.foot-follow h4{font-size:16px;font-weight:600;margin-bottom:10px}
.foot-follow p{font-size:14px;color:#444;line-height:1.7}
.socials{left:240px;top:4360px;display:flex;gap:12px}
.socials i{width:30px;height:30px;border-radius:50%;background:var(--ink);display:block}
.foot-links{left:740px;top:4236px}
.foot-links h4{font-size:16px;font-weight:600;margin-bottom:16px}
.foot-cols{display:flex;gap:90px}
.foot-cols ul{list-style:none;font-size:13px;line-height:2.05;color:#333;text-transform:uppercase}
.foot-cols li::before{content:"";display:inline-block;width:7px;height:7px;border-radius:50%;background:var(--coral);margin-right:14px;vertical-align:middle}
.copyright{left:0;top:4482px;width:1200px;text-align:center;font-size:13px;color:#333;letter-spacing:.5px}
</style>
</head>
<body>

<svg class="backdrop" viewBox="0 0 1200 4596" aria-hidden="true">
  <defs>
    <linearGradient id="topwash" x1="0" y1="0" x2="1" y2="1">
      <stop offset="0" stop-color="#fde3e5"/><stop offset="1" stop-color="#f9b4ba"/>
    </linearGradient>
    <linearGradient id="midwash" x1="0" y1="0" x2="0" y2="1">
      <stop offset="0" stop-color="#ffffff"/><stop offset=".25" stop-color="#fde4e6"/>
      <stop offset=".7" stop-color="#fcd2d5"/><stop offset="1" stop-color="#f9b6bc"/>
    </linearGradient>
    <linearGradient id="lowwash" x1="0" y1="0" x2="0" y2="1">
      <stop offset="0" stop-color="#ffffff"/><stop offset=".45" stop-color="#fde0e2"/>
      <stop offset="1" stop-color="#f8aeb4"/>
    </linearGradient>
  </defs>
  <path d="M520 0 H1200 V260 C1120 210 1020 200 900 150 C760 95 620 90 520 0 Z" fill="url(#topwash)"/>
  <path d="M0 1060 C300 1120 700 1040 1200 1080 V2800 C900 2900 500 2830 0 2880 Z" fill="url(#midwash)"/>
  <path d="M0 3560 C400 3600 800 3540 1200 3580 V4230 C900 4150 500 4160 0 4210 Z" fill="url(#lowwash)"/>
  <path d="M0 4200 C380 4130 820 4150 1200 4210 V4596 H0 Z" fill="#ffffff"/>
</svg>

<!-- header -->
<div class="abs brand">BRIGHT<br>NEIGHBOUR</div>
<nav class="abs nav">
  <a class="active" href="#">Home</a><a href="#">About Us</a><a href="#">Our Story</a><a href="#">Social Impact</a>
</nav>
<div class="abs btn-dark join">JOIN US</div>

<!-- hero -->
<section class="abs hero-text">
  <div class="eyebrow">Who we are</div>
  <h1 class="h-xl">About Us</h1>
  <p class="lead">If you can't pay<br>back Pay it forward</p>
</section>
<div class="abs hero-photo" role="img" aria-label="Photo of a smiling team working together at laptops"></div>
<div class="abs badge" role="img" aria-label="Partner badge"></div>

<!-- values -->
<article class="abs card" style="left:100px">
  <h3>Our Philosophy</h3>
  <p>We believe in authentic social responsibility is driven from individuals and businesses.</p>
</article>
<article class="abs card" style="left:450px">
  <h3>Our Mission</h3>
  <p>We connect individuals and businesses to support others it needs most in an easy, transparent, and holistic way through our platform.</p>
</article>
<article class="abs card" style="left:800px">
  <h3>Our Future</h3>
  <p>Together, social impact as part of DNA at the heart of every consumption and business.</p>
</article>

<!-- contributors 1 -->
<div class="abs disc" style="left:100px;top:1140px;width:440px;height:440px;background:var(--pink-mid)"></div>
<div class="abs phone" style="left:235px;top:1185px" role="img" aria-label="App screen showing the contributor home page"></div>
<section class="abs involve" style="left:652px;top:1176px">
  <div class="eyebrow">Getting involved</div>
  <h2 class="h-lg">Contributors</h2>
  <p class="body-text">You can Pay-it-forward products and services listings on our platform just like any other e-commerce platform with Bright Messages.</p>
  <p class="body-text">The platform will match with beneficiary who require the contributions with the personalized message.</p>
  <p class="body-text">Contributor will receive an alert once the beneficiary claims their contributions.</p>
</section>

<!-- merchants -->
<section class="abs involve" style="left:100px;top:1720px">
  <div class="eyebrow">Getting involved</div>
  <h2 class="h-lg">Merchants</h2>
  <p class="body-text">Our free listing platform allows Merchants to upload and list the available goods and services.</p>
  <p class="body-text">Beneficiary or their representative make the booking and contact the merchant to claim the contributions directly with redemption code verifications.</p>
</section>
<div class="abs disc" style="left:648px;top:1660px;width:440px;height:440px;background:var(--butter)"></div>
<div class="abs phone" style="left:783px;top:1705px" role="img" aria-label="App screen showing merchant listings"></div>

<!-- contributors 2 -->
<div class="abs disc" style="left:60px;top:2280px;width:440px;height:440px;background:var(--peach)"></div>
<div class="abs phone" style="left:195px;top:2325px" role="img" aria-label="App screen showing community partners"></div>
<section class="abs involve" style="left:612px;top:2264px">
  <div class="eyebrow">Getting involved</div>
  <h2 class="h-lg">Contributors</h2>
  <p class="body-text">You can Pay-it-forward products and services listings on our platform just like any other e-commerce platform with Bright Messages.</p>
  <p class="body-text">The platform will match with beneficiary who require the contributions with the personalized message.</p>
  <p class="body-text">Contributor will receive an alert once the beneficiary claims their contributions.</p>
</section>

<!-- faq -->
<section class="abs faq-head">
  <div class="eyebrow">What's on your mind</div>
  <h2 class="h-lg">Frequently Asked Question</h2>
  <p class="body-text" style="font-size:14px;line-height:1.5">Everyday has its share of challenging moments. Anyone can experience tough times in their life. That's why we need timely help.</p>
</section>
<div class="abs faq-list">
  <div class="faq-item">What's so unique about the social impact?</div>
  <div class="faq-item">How is this different from other government or NGO initiatives?</div>
  <div class="faq-item">Are you able to issue tax-deductible receipts?</div>
  <div class="faq-item">What is the legitimacy behind the concept of your organization?</div>
  <div class="faq-item">Do you accept lump sum cash contributions?</div>
  <div class="faq-item">Will contributors get updates on how their contributions are used?</div>
  <div class="faq-item">Will the beneficiaries know the personal details of contributors?</div>
  <div class="faq-item">Can a contributor choose a specific beneficiary?</div>
</div>
<div class="abs faq-photo" role="img" aria-label="Photo of a cheerful woman talking on the phone"></div>

<!-- newsletter -->
<h2 class="abs sub-title">Subscribe<br><span>to Our Newsletter</span></h2>
<p class="abs sub-blurb">Let's stay in touch! We would like to keep you inspired with our kindness stories and community events.</p>
<div class="abs field" style="left:500px;width:300px">Email</div>
<div class="abs field" style="left:828px;width:272px">Name</div>
<div class="abs consent"><i></i>By continuing, you accept the privacy policy</div>
<div class="abs btn-dark subscribe">SUBSCRIBE</div>

<!-- footer -->
<div class="abs foot-brand">BRIGHT<br>NEIGHBOUR</div>
<div class="abs foot-follow">
  <h4>Follow us and stay updated!</h4>
  <p>A Singapore Social Enterprise<br>In a world where you can be anything, be kind</p>
</div>
<div class="abs socials"><i></i><i></i><i></i></div>
<div class="abs foot-links">
  <h4>Get To Know Us</h4>
  <div class="foot-cols">
    <ul><li>Home</li><li>About Us</li><li>Our Story</li><li>Social Impact</li><li>Bright Neighbour</li></ul>
    <ul><li>Bright Business</li><li>Merchant</li><li>The BrightGift</li><li>FAQs</li><li>Contact Us</li></ul>
  </div>
</div>
<div class="abs copyright">COPYRIGHT © 2021 BRIGHT NEIGHBOUR SINGAPORE</div>

</body>
</html>
```